Business Card Design Project

Business Card
We are rebranding with a new logo
Industry/Entity Type
Business
Contact Information for Business Card
Dennis Morvale +61 487215963 dennis@quorv.com.au P.O. Box 872 Fernlow QLD 4309
Requirements
Must have
- Logo

```html
<!DOCTYPE html>
<html lang="en">
<head>
<meta charset="utf-8">
<title>Quorv International – Business Card</title>
<link href="https://fonts.googleapis.com/css2?family=Source+Sans+3:wght@400;600;700&display=swap" rel="stylesheet">
<style>
  :root {
    --backdrop: #2b2c2f;
    --card-white: #f7f7f5;
    --brand-orange: #ee8a1f;
    --brand-orange-deep: #e0741a;
    --brand-blue: #0f7fae;
    --brand-blue-deep: #0a5b80;
    --brand-blue-light: #1ea0d2;
    --text-light: #ffffff;
  }
  * { box-sizing: border-box; margin: 0; padding: 0; }
  html, body {
    width: 1200px; height: 960px; overflow: hidden;
    background: var(--backdrop);
    font-family: "Source Sans 3", "Myriad Pro", Arial, sans-serif;
  }
  .sheet {
    position: relative; width: 1200px; height: 960px;
  }
  .card {
    position: absolute; left: 250px; width: 700px; height: 400px;
    overflow: hidden; border-radius: 4px;
    box-shadow: 0 12px 30px rgba(0,0,0,.45);
  }
  /* Back of card */
  .card--back {
    top: 50px;
    background: var(--brand-orange);
    display: flex; flex-direction: column; align-items: center; justify-content: center;
    color: var(--text-light);
  }
  .card--back .wordmark { color: var(--text-light); }
  .card--back .website {
    margin-top: 34px; font-size: 17px; letter-spacing: 5px; font-weight: 400;
  }
  /* Wordmark */
  .wordmark {
    display: flex; align-items: center; gap: 16px;
    font-weight: 700; line-height: 1;
  }
  .wordmark__dot {
    width: 22px; height: 22px; border-radius: 50%; background: currentColor;
  }
  .wordmark__text { display: flex; flex-direction: column; }
  .wordmark__name { font-size: 74px; letter-spacing: 1px; }
  .wordmark__tag { font-size: 22px; letter-spacing: 5px; margin-top: 6px; }
  /* Front of card */
  .card--front {
    top: 510px; background: var(--card-white);
  }
  .card__wave { position: absolute; inset: 0; }
  .card--front .wordmark {
    position: absolute; left: 56px; top: 90px; color: var(--brand-blue);
  }
  .contact {
    position: absolute; right: 40px; bottom: 36px;
    text-align: right; color: var(--text-light);
    font-size: 19px; line-height: 25px;
  }
  .contact__name {
    color: var(--brand-orange); font-weight: 700; font-size: 20px;
    letter-spacing: .5px; margin-bottom: 12px; text-transform: uppercase;
  }
  .contact__line { display: flex; justify-content: flex-end; align-items: center; gap: 8px; }
  .contact__icon { width: 16px; height: 16px; flex: none; }
</style>
</head>
<body>
<main class="sheet">

  <section class="card card--back" aria-label="Card back">
    <div class="wordmark">
      <span class="wordmark__text">
        <span class="wordmark__name">Quorv</span>
        <span class="wordmark__tag">INTERNATIONAL</span>
      </span>
    </div>
    <p class="website">www.quorv.com.au</p>
  </section>

  <section class="card card--front" aria-label="Card front">
    <svg class="card__wave" viewBox="0 0 700 400" preserveAspectRatio="none">
      <defs>
        <radialGradient id="blueGlow" cx="0.72" cy="0.45" r="0.7">
          <stop offset="0" stop-color="var(--brand-blue-light)"/>
          <stop offset="0.6" stop-color="var(--brand-blue)"/>
          <stop offset="1" stop-color="var(--brand-blue-deep)"/>
        </radialGradient>
      </defs>
      <path d="M455 0 C520 80 470 170 390 230 C300 300 260 350 232 400 L700 400 L700 0 Z" fill="var(--brand-orange-deep)"/>
      <path d="M470 0 C535 80 485 175 405 235 C320 300 280 350 252 400 L700 400 L700 0 Z" fill="url(#blueGlow)"/>
    </svg>

    <div class="wordmark">
      <span class="wordmark__dot"></span>
      <span class="wordmark__text">
        <span class="wordmark__name">Quorv</span>
        <span class="wordmark__tag">INTERNATIONAL</span>
      </span>
    </div>

    <address class="contact" style="font-style:normal">
      <p class="contact__name">Dennis Morvale</p>
      <p class="contact__line">P.O. Box 872</p>
      <p class="contact__line">Fernlow QLD 4309</p>
      <p class="contact__line">+61 487215963
        <svg class="contact__icon" viewBox="0 0 16 16"><path d="M4 2l2.5 3-1.5 1.5c.8 1.8 2.2 3.2 4 4L10.5 9 13.5 11.5 12 14C7 14 2 9 2 4z" fill="var(--brand-orange)"/></svg>
      </p>
      <p class="contact__line">dennis@quorv.com.au
        <svg class="contact__icon" viewBox="0 0 16 16"><rect x="1.5" y="3.5" width="13" height="9" rx="1" fill="var(--brand-orange)"/><path d="M2 4l6 5 6-5" fill="none" stroke="var(--brand-blue)" stroke-width="1.2"/></svg>
      </p>
      <p class="contact__line">www.quorv.com.au
        <svg class="contact__icon" viewBox="0 0 16 16"><circle cx="8" cy="8" r="6.5" fill="var(--brand-orange)"/><path d="M1.5 8h13M8 1.5c-3 3.5-3 9.5 0 13M8 1.5c3 3.5 3 9.5 0 13" fill="none" stroke="var(--brand-blue)" stroke-width="1"/></svg>
      </p>
    </address>
  </section>

</main>
</body>
</html>
```